HearthMile business card and stationary design

We are looking for a simple yet elegant design for our mortgage company business card and stationary.

The card should include:
Name (Marcus Pell)
Title (CEO)
Phone Number (732-555-0182)
Address (48 Birchwell Court, Suite 314, Ashvale, NJ 07999)
Email (email@hearthmile.example)
"NMLS" i.e. (NMLS 61947)
"Company NMLS" (Company NMLS 274615)

Contact Information for Business Card

See above

```html
<!DOCTYPE html>
<html lang="en">
<head>
<meta charset="utf-8">
<title>HearthMile Business Card</title>
<link href="https://fonts.googleapis.com/css2?family=Montserrat:wght@600;700&family=Lato:wght@400;700&display=swap" rel="stylesheet">
<style>
  :root {
    --backdrop: #e4e4e4;
    --paper: #f7f7f7;
    --navy: #1f2a37;
    --ink: #1d2632;
    --accent: #11a3e8;
    --muted: #9a9a9a;
    --white: #ffffff;
  }
  * { box-sizing: border-box; margin: 0; padding: 0; }
  html, body { width: 1200px; height: 930px; overflow: hidden; }
  body {
    background: var(--backdrop);
    font-family: "Lato", sans-serif;
    color: var(--ink);
  }
  .sheet {
    width: 1200px; height: 930px;
    display: flex; align-items: center; justify-content: center; gap: 40px;
  }
  .card {
    width: 540px; height: 309px;
    position: relative;
    box-shadow: 0 10px 26px rgba(0,0,0,0.12);
  }
  .card--front { background: var(--paper); }
  .card--back { background: var(--navy); color: var(--white); }

  .wordmark {
    font-family: "Montserrat", sans-serif;
    font-weight: 700;
    font-size: 54px;
    letter-spacing: 1px;
    line-height: 1;
    display: flex; align-items: center; gap: 12px;
  }
  .wordmark__dot { width: 12px; height: 12px; border-radius: 50%; }
  .card--front .wordmark { position: absolute; left: 118px; top: 60px; color: var(--ink); }
  .card--front .wordmark__dot { background: var(--accent); }
  .card--back .wordmark { position: absolute; left: 118px; top: 112px; color: var(--white); }
  .card--back .wordmark__dot { background: var(--white); }

  .person { position: absolute; left: 60px; top: 150px; text-align: right; width: 170px; }
  .person__name { font-family: "Montserrat", sans-serif; font-weight: 700; font-size: 20px; color: var(--ink); }
  .person__name-last { color: var(--accent); }
  .person__title { font-size: 14px; margin-top: 2px; }

  .divider { position: absolute; left: 250px; top: 150px; width: 1px; height: 58px; background: var(--muted); }

  .contacts { position: absolute; left: 268px; top: 150px; list-style: none; font-size: 14px; }
  .contacts li { display: flex; align-items: center; gap: 8px; height: 19px; }
  .contacts svg { width: 12px; height: 12px; fill: var(--accent); flex: none; }

  .address {
    position: absolute; left: 60px; top: 232px;
    display: flex; align-items: center; gap: 8px; font-size: 14px;
  }
  .address svg { width: 11px; height: 14px; fill: var(--accent); }

  .licence {
    position: absolute; left: 122px; top: 196px;
    font-size: 13px; letter-spacing: 0.6px;
  }
</style>
</head>
<body>
<main class="sheet">
  <section class="card card--front" aria-label="Card front">
    <div class="wordmark"><span class="wordmark__dot"></span>HearthMile</div>

    <div class="person">
      <p class="person__name">Marcus <span class="person__name-last">Pell</span></p>
      <p class="person__title">CEO</p>
    </div>

    <div class="divider"></div>

    <ul class="contacts">
      <li>
        <svg viewBox="0 0 24 24"><path d="M6.6 10.8a15.1 15.1 0 0 0 6.6 6.6l2.2-2.2a1 1 0 0 1 1-.25 11.4 11.4 0 0 0 3.6.57 1 1 0 0 1 1 1V20a1 1 0 0 1-1 1A17 17 0 0 1 3 4a1 1 0 0 1 1-1h3.5a1 1 0 0 1 1 1c0 1.25.2 2.45.57 3.6a1 1 0 0 1-.25 1z"/></svg>
        732-555-0182
      </li>
      <li>
        <svg viewBox="0 0 24 24"><path d="M2 5h20v14H2z"/><path d="M2 5l10 8 10-8v1.5l-10 8-10-8z" fill="#f7f7f7"/></svg>
        email@hearthmile.example
      </li>
      <li>
        <svg viewBox="0 0 24 24"><circle cx="12" cy="12" r="10"/><path d="M2 12h20M12 2c3 3 3 17 0 20M12 2c-3 3-3 17 0 20" stroke="#f7f7f7" stroke-width="1.5" fill="none"/></svg>
        www.hearthmile.example
      </li>
    </ul>

    <p class="address">
      <svg viewBox="0 0 20 26"><path d="M10 0a9 9 0 0 0-9 9c0 7 9 17 9 17s9-10 9-17a9 9 0 0 0-9-9zm0 12.5A3.5 3.5 0 1 1 10 5.5a3.5 3.5 0 0 1 0 7z"/></svg>
      48 Birchwell Court, Suite 314, Ashvale, NJ 07999
    </p>
  </section>

  <section class="card card--back" aria-label="Card back">
    <div class="wordmark"><span class="wordmark__dot"></span>HearthMile</div>
    <p class="licence">NMLS 61947 | Company NMLS 274615</p>
  </section>
</main>
</body>
</html>
```